Design of a nice Video On Demand Website

We are looking to design a nice Website for our Video On demand platform we are getting ready to launch. We have put together a file to illustrate the idea and design concept we want. The file also has the menu sections ect. The Designers should look at the file and suggest design ideas based on the concept we put together on the file. The design should be clean yet simple so users can experience a better Navigation. The designer is free to choose whatever color he thinks fit.
Updates

Need extra days to review

Sick

Target Market(s)

Streaming

Number of Pages Required

1 page

Font styles to use
Sans Serif

Colors

Designer to choose colors to be used in the design.

Requirements
Must have
• I will let the designer choose what is best.
Nice to have
Should not have

```html
<!DOCTYPE html>
<html lang="en">
<head>
<meta charset="utf-8">
<title>Lumo – Video On Demand</title>
<link rel="stylesheet" href="https://fonts.googleapis.com/css2?family=Nunito+Sans:wght@400;600;700;800&display=swap">
<style>
  :root {
    --sidebar-bg: #1c1c1c;
    --panel-bg: #2e2e2e;
    --user-bg: #383838;
    --divider: #2a2a2a;
    --accent: #f47a35;
    --text: #ffffff;
    --text-soft: #e6e6e6;
    --channel-bg: #2b2b2b;
    --hero-dark: #0d1a1f;
    --hero-mid: #3b6270;
    --hero-light: #8fb3c2;
    --online: #3ccf4e;
  }
  * { box-sizing: border-box; margin: 0; padding: 0; }
  html, body {
    width: 1200px; height: 750px; overflow: hidden;
    background: var(--sidebar-bg);
    font-family: "Nunito Sans", sans-serif;
    color: var(--text);
  }
  .app { position: relative; width: 1200px; height: 750px; }

  /* Sidebar */
  .sidebar {
    position: absolute; left: 0; top: 0; width: 167px; height: 750px;
    background: var(--sidebar-bg);
  }
  .brand {
    height: 101px; border-bottom: 1px solid var(--divider);
    display: flex; align-items: center; justify-content: center; gap: 7px;
  }
  .brand-mark { width: 14px; height: 14px; background: var(--accent); }
  .brand-name { font-size: 24px; font-weight: 800; color: var(--text); letter-spacing: .5px; }
  .search-wrap { height: 59px; display: flex; align-items: center; padding: 0 10px; }
  .search {
    width: 146px; height: 27px; border-radius: 14px; background: var(--panel-bg);
    display: flex; align-items: center; justify-content: space-between; padding: 0 10px 0 17px;
    font-size: 13.5px; color: #cfcfcf;
  }
  .user {
    height: 66px; background: var(--user-bg);
    display: flex; align-items: center; padding-left: 24px; gap: 6px;
  }
  .avatar { position: relative; width: 33px; height: 33px; }
  .avatar-photo {
    width: 33px; height: 33px; border-radius: 50%;
    background: linear-gradient(160deg, #8a8a8a, #4a4a4a);
  }
  .avatar-status {
    position: absolute; right: 1px; top: 0; width: 8px; height: 8px;
    border-radius: 50%; background: var(--online);
  }
  .user-name { font-size: 14px; font-weight: 600; }
  .user-caret { margin-left: 10px; }
  .nav { list-style: none; padding: 23px 0 0 29px; }
  .nav li { height: 43px; font-size: 13.5px; font-weight: 600; color: var(--text-soft); }
  .nav li.active { color: var(--accent); }
  .legal { position: absolute; left: 22px; bottom: 20px; list-style: none; }
  .legal li { font-size: 11px; color: var(--text-soft); height: 27px; }

  /* Hero */
  .hero {
    position: absolute; left: 167px; top: 0; width: 1033px; height: 673px; overflow: hidden;
  }
  .hero-photo {
    position: absolute; inset: 0;
    background:
      radial-gradient(ellipse at 55% 55%, var(--hero-light) 0%, transparent 45%),
      radial-gradient(ellipse at 85% 40%, #6f93a2 0%, transparent 40%),
      linear-gradient(90deg, #2a3d46 0%, var(--hero-mid) 50%, #26404b 80%, var(--hero-dark) 100%);
  }
  .hero-shade {
    position: absolute; inset: 0;
    background: linear-gradient(90deg, rgba(0,0,0,.35) 0%, rgba(0,0,0,.1) 55%, rgba(0,0,0,0) 100%);
  }
  .hero-content { position: absolute; left: 51px; top: 218px; width: 450px; }
  .hero-title { font-size: 44px; font-weight: 800; line-height: 1; letter-spacing: -.5px; }
  .hero-subtitle { margin-top: 14px; width: 370px; font-size: 25px; font-weight: 400; line-height: 30px; }
  .hero-text { margin-top: 13px; width: 445px; font-size: 16px; line-height: 23.3px; }
  .watch-btn {
    margin-top: 27px; width: 155px; height: 40px; border-radius: 20px;
    background: var(--accent); display: flex; align-items: center; padding-left: 6px; gap: 11px;
    font-size: 17px; font-weight: 600; color: var(--text);
  }

  /* Channel strip */
  .channels {
    position: absolute; left: 167px; top: 673px; width: 1033px; height: 77px;
    background: var(--channel-bg);
    display: flex; align-items: center; justify-content: space-between; padding: 0 25px 0 24px;
  }
  .channel { font-size: 19px; font-weight: 800; color: var(--text); white-space: nowrap; }
  .channel-wide { font-size: 27px; }
</style>
</head>
<body>
<div class="app">
  <aside class="sidebar">
    <div class="brand"><span class="brand-mark"></span><span class="brand-name">Lumo</span></div>
    <div class="search-wrap">
      <div class="search">
        <span>Search</span>
        <svg width="14" height="14" viewBox="0 0 14 14"><circle cx="5.8" cy="5.8" r="4.6" fill="none" stroke="#fff" stroke-width="1.7"/><line x1="9.2" y1="9.2" x2="13" y2="13" stroke="#fff" stroke-width="1.8" stroke-linecap="round"/></svg>
      </div>
    </div>
    <div class="user">
      <div class="avatar">
        <div class="avatar-photo" role="img" aria-label="Profile photo of the signed-in user"></div>
        <span class="avatar-status"></span>
      </div>
      <span class="user-name">John Doe</span>
      <svg class="user-caret" width="10" height="6" viewBox="0 0 10 6"><path d="M0 0h10L5 6z" fill="#fff"/></svg>
    </div>
    <ul class="nav">
      <li class="active">Programme Guide</li>
      <li>My Selection</li>
      <li>Entertainment</li>
      <li>Series</li>
      <li>News</li>
      <li>Sports</li>
      <li>Comedy</li>
      <li>Kids</li>
      <li>TV Movies</li>
    </ul>
    <ul class="legal">
      <li>Privacy Police</li>
      <li>Terms &amp; Conditions</li>
    </ul>
  </aside>

  <section class="hero">
    <div class="hero-photo" role="img" aria-label="Cooking show cast in chef whites posing in a professional kitchen"></div>
    <div class="hero-shade"></div>
    <div class="hero-content">
      <h1 class="hero-title">KITCHEN MASTERS</h1>
      <h2 class="hero-subtitle">The modern casserole of Marc Delorme</h2>
      <p class="hero-text">Lorem ipsum dolor sit amet, consectetur adipiscing elit. Integer id nibh est. Vivamus tincidunt sem eu volutpat porttitor. Donec tincidunt ac justo vel pellentesque. Praesent congue finibus erat eget luctus. Aenean sed mi nec elit volutpat pulvinar.</p>
      <div class="watch-btn">
        <svg width="29" height="29" viewBox="0 0 29 29"><circle cx="14.5" cy="14.5" r="13" fill="none" stroke="#fff" stroke-width="1.6"/><circle cx="14.5" cy="14.5" r="11.4" fill="#fff"/><path d="M12 9.5v10l8-5z" fill="#f47a35"/></svg>
        <span>Watch now</span>
      </div>
    </div>
  </section>

  <nav class="channels">
    <span class="channel">Lumo 1</span>
    <span class="channel">Lumo 2</span>
    <span class="channel">Lumo 3</span>
    <span class="channel">Lumo City</span>
    <span class="channel">Radio Lumo</span>
    <span class="channel">Onda 2</span>
    <span class="channel">Radio Live</span>
    <span class="channel channel-wide">Lumo.news</span>
  </nav>
</div>
</body>
</html>
```